Business Card Design Project

Basic business card with minimal details. I just need company name, email & web address, telephone and my name.
I would like the back of the card to be grey with my logo & company name centred.

Target Market(s)

Architects
Builders
Property Developers

Industry/Entity Type

Business

Font styles to use
Sans Serif

Colors

Designer to choose colors to be used in the design.

Requirements
Must have
• Tallow Crest
Rupert Hazelby - Director
M: 0427 915203
E: rupert@tallowcrest.com.au
W: www.tallowcrest.com.au
Should not have
• No other images or pictures

```html
<!DOCTYPE html>
<html lang="en">
<head>
<meta charset="utf-8">
<title>Tallow Crest – Business Card</title>
<link href="https://fonts.googleapis.com/css2?family=Open+Sans:wght@400;600&display=swap" rel="stylesheet">
<style>
  :root {
    --page-bg: #f4f4f4;
    --card-bg: #e8e8e8;
    --card-bg-light: #efefef;
    --slate: #6b7480;
    --ink: #3d4852;
    --crimson: #a81c3a;
    --white: #ffffff;
  }
  html, body {
    margin: 0;
    padding: 0;
    width: 1200px;
    height: 864px;
    overflow: hidden;
    background: var(--page-bg);
    font-family: "Open Sans", Arial, sans-serif;
  }
  .card {
    position: absolute;
    left: 100px;
    top: 132px;
    width: 1000px;
    height: 600px;
    background: linear-gradient(135deg, var(--card-bg-light), var(--card-bg));
    box-shadow: 0 12px 30px rgba(0,0,0,0.18);
    overflow: hidden;
  }
  .card-graphics {
    position: absolute;
    inset: 0;
  }
  .brand {
    position: absolute;
    left: 40px;
    top: 300px;
    display: flex;
    align-items: center;
    gap: 16px;
  }
  .brand-mark {
    width: 26px;
    height: 26px;
    background: var(--crimson);
  }
  .brand-name {
    font-weight: 600;
    font-size: 40px;
    letter-spacing: 2px;
    color: var(--ink);
    text-transform: uppercase;
  }
  .person {
    position: absolute;
    left: 590px;
    top: 88px;
    color: var(--crimson);
  }
  .person-name {
    font-weight: 600;
    font-size: 30px;
    letter-spacing: 1px;
    text-transform: uppercase;
    line-height: 1.1;
  }
  .person-role {
    font-weight: 400;
    font-size: 18px;
    line-height: 1.2;
  }
  .contact-line {
    position: absolute;
    color: var(--white);
    font-size: 19px;
    font-weight: 400;
    letter-spacing: 0.5px;
    height: 44px;
    line-height: 44px;
  }
  .contact-web { left: 635px; top: 400px; }
  .contact-email { left: 653px; top: 452px; }
  .contact-phone { left: 671px; top: 504px; }
</style>
</head>
<body>
  <div class="card">
    <svg class="card-graphics" width="1000" height="600" viewBox="0 0 1000 600" aria-hidden="true">
      <polygon class="divider-stripe" points="373,0 387,0 597,600 583,600" fill="var(--slate)"/>
      <polygon class="contact-band" points="600,400 1000,400 1000,444 615.4,444" fill="var(--crimson)"/>
      <polygon class="contact-band" points="618.2,452 1000,452 1000,496 633.6,496" fill="var(--crimson)"/>
      <polygon class="contact-band" points="636.4,504 1000,504 1000,548 651.8,548" fill="var(--crimson)"/>
      <g class="icon-monitor" fill="none" stroke="var(--ink)" stroke-width="2">
        <rect x="555" y="413" width="22" height="15" rx="1"/>
        <line x1="566" y1="428" x2="566" y2="433"/>
        <line x1="560" y1="434" x2="572" y2="434"/>
      </g>
      <g class="icon-envelope" fill="none" stroke="var(--ink)" stroke-width="2">
        <rect x="575" y="466" width="22" height="16"/>
        <polyline points="575,466 586,476 597,466"/>
      </g>
      <g class="icon-phone" fill="none" stroke="var(--ink)" stroke-width="2">
        <rect x="598" y="515" width="13" height="22" rx="2"/>
        <line x1="602" y1="533" x2="607" y2="533"/>
      </g>
    </svg>

    <div class="brand">
      <div class="brand-mark"></div>
      <div class="brand-name">Tallow Crest</div>
    </div>

    <div class="person">
      <div class="person-name">Rupert Hazelby</div>
      <div class="person-role">Director</div>
    </div>

    <div class="contact-line contact-web">www.tallowcrest.com.au</div>
    <div class="contact-line contact-email">rupert@tallowcrest.com.au</div>
    <div class="contact-line contact-phone">0427 915203</div>
  </div>
</body>
</html>
```